Corvane Card

The logo is the Spanish flag colors I want a vibrant eye catching design with the yellow / red colors over either Navy or white background or black even ,
Would like a 2D feel to the logo with another lighter color logo under it look ,

Contact Information for Business Card

Corvane Flooring
Teodor Vashkin
Main Number
Cell Number
Fax Number

Website on the side of the card somewhere

Font styles to use
Sans Serif

Colors
ec1f27
ffc214

Requirements
Must have
• 2 logos feel one is bolder and the other one underneath very light

```html
<!DOCTYPE html>
<html lang="en">
<head>
<meta charset="utf-8">
<title>Corvane Flooring – Business Card</title>
<link href="https://fonts.googleapis.com/css2?family=Ubuntu:wght@500;700&family=Arimo:wght@400&display=swap" rel="stylesheet">
<style>
  :root {
    --navy: #01112e;
    --red: #ec1f27;
    --yellow: #ffc214;
    --white: #ffffff;
    --backdrop: #e4e4e4;
  }
  * { margin: 0; padding: 0; box-sizing: border-box; }
  html, body {
    width: 1200px;
    height: 900px;
    overflow: hidden;
    background: var(--backdrop);
  }
  .card {
    position: absolute;
    top: 217px;
    width: 309px;
    height: 500px;
    background: var(--navy);
    color: var(--white);
  }
  .card--front {
    left: 279px;
    border-radius: 0 70px 0 70px;
  }
  .card--back {
    left: 617px;
    border-radius: 70px 0 70px 0;
  }
  .brand {
    position: absolute;
    left: 0;
    width: 100%;
    display: flex;
    flex-direction: column;
    align-items: center;
  }
  .card--front .brand { top: 174px; }
  .card--back .brand { top: 96px; }
  .brand__mark {
    width: 46px;
    height: 46px;
    background: var(--yellow);
    margin-bottom: 44px;
  }
  .brand__name {
    font-family: "Ubuntu", sans-serif;
    font-weight: 700;
    color: var(--red);
    text-align: center;
    text-transform: uppercase;
    font-size: 37px;
    line-height: 1;
    letter-spacing: 1px;
  }
  .brand__name span {
    display: block;
    font-size: 17px;
    letter-spacing: 15px;
    margin-top: 12px;
    margin-right: -15px;
  }
  .person {
    position: absolute;
    left: 34px;
    top: 322px;
    font-family: "Ubuntu", sans-serif;
    font-weight: 500;
    font-size: 21px;
    text-transform: uppercase;
    color: var(--red);
  }
  .person__surname { color: var(--yellow); }
  .contacts {
    position: absolute;
    left: 32px;
    top: 362px;
    list-style: none;
    font-family: "Arimo", sans-serif;
    font-size: 15px;
    line-height: 18px;
  }
  .contacts li {
    display: flex;
    align-items: center;
    gap: 5px;
  }
  .contacts svg {
    width: 13px;
    height: 13px;
    fill: var(--red);
    flex: none;
  }
  .highlight { color: var(--red); }
</style>
</head>
<body>
  <section class="card card--front" aria-label="Card front">
    <div class="brand">
      <div class="brand__mark"></div>
      <p class="brand__name">Corvane<span>Flooring</span></p>
    </div>
  </section>

  <section class="card card--back" aria-label="Card back">
    <div class="brand">
      <div class="brand__mark"></div>
      <p class="brand__name">Corvane<span>Flooring</span></p>
    </div>

    <p class="person">Teodor <span class="person__surname">Vashkin</span></p>

    <ul class="contacts">
      <li>
        <svg viewBox="0 0 16 16" aria-hidden="true"><path d="M1 5c0-2 3-3 7-3s7 1 7 3v1h-4V5H5v1H1z M4 7h8l2 7H2z"/></svg>
        312 555 0147
      </li>
      <li>
        <svg viewBox="0 0 16 16" aria-hidden="true"><path d="M4 0h8a1 1 0 0 1 1 1v14a1 1 0 0 1-1 1H4a1 1 0 0 1-1-1V1a1 1 0 0 1 1-1zm1 2v10h6V2zm3 11a1 1 0 1 0 0 2 1 1 0 0 0 0-2z"/></svg>
        312 555 0198
      </li>
      <li>
        <svg viewBox="0 0 16 16" aria-hidden="true"><path d="M4 0h8v4H4z M1 5h14v7h-3v-2H4v2H1z M5 11h6v5H5z"/></svg>
        312 555 0163
      </li>
      <li>
        <svg viewBox="0 0 16 16" aria-hidden="true"><path d="M0 3h16v10H0z M1.5 4.5 8 9l6.5-4.5" stroke="#01112e" stroke-width="1.3"/></svg>
        hello@corvane.com
      </li>
      <li>
        <svg viewBox="0 0 16 16" aria-hidden="true"><circle cx="8" cy="8" r="7.5"/><path d="M4 4c2 0 3 2 2 3s-1 3 1 4M10 2c0 2 2 2 3 3" stroke="#01112e" stroke-width="1.2" fill="none"/></svg>
        <span>www.<span class="highlight">corvanefloors</span>.com</span>
      </li>
    </ul>
  </section>
</body>
</html>
```